Ecological Cosmetics (w/ Social Impact) Website

Dr. Wendelin Marovitz Naturprodukte KELVORA®, a small family-run ecological cosmetics “start-up” business (has been around since the mid 90s but only now beginning professionalize management), wishes to redesign its web presence, as part of a comprehensive “facelift” that will also encompass at a later stage its corporate identity (e.g. logo…).
We would like to prepare a new trilingual (later 3 additional languages will be added) website (www.kelvora7.at) that is symbiotic with web 2.0 enabled interwoven with a blog, news section, social networks integrated (e.g. preference/like buttons, Friendbook), changing images and announcements appearing on first page, online payment services, mobile internet compatibility (e.g. iOS, Android, BlackBerry… thus no use of Flash, no need for a specific app), etc. and all the other significant trends in the e-commerce realm. The website should be easily and quickly accessible, fun to navigate, allow us to update it simply (through a content manager) and so “sexy” that people will want to return to the web, inform themselves of events and news, and hopefully also try our products.
Our company is based in Austria and specializes in the production of organic cosmetics in the mid-upper pricing range. We pride ourselves in offering natural cosmetics (the meaning of “natural” is relative and each person may have a different definition), with no petrochemical preservatives. Some of our products, such as the mineral salts and black mud powder from the Dead Sea cannot be obtained more naturally, unless you actually visit the area, thus retain all their properties. Our products are not medicine but the basic Dead Sea ingredients are used by spas and clinics in the area to treat many different skin, joint and bone affections. Our male and female customers (no distinction made will be made on our new website), primarily as of the ages of 25 to 65, buy KELVORA® because they:
• Care about the exterior and interior well-being
• Wish to look well cared, preserve their skin’s flexibility, natural splendor & properties
• Prefer natural skin care
• Nourish their skin with vital minerals/trace elements, protecting/treating their skin with natural ingredients
• Willing to pay more than average for natural cosmetics, looking for quality,
• Don’t mind spending about 15 minutes per week preparing a mud mask with some hot water.
• Bathe in water enriched with mineral salts
• Know or are surprised to find out that Dead Sea mud is one of the few, if not the only, naturally astringent (tenses the skin) muds in the world
• Help alleviate skin conditions (e.g. psoriasis, dermatitis, acne, eczema, pustules, oily skin ...), joint (e.g. rheumatism, arthritis ...) and cardiovascular disease.
Amongst the minerals in many of our products (particularly salt, mud), are sulfur and zinc, two naturally disinfecting and healing minerals, thus their common use in many dermatological drugs. Both salt and mud powder are completely natural, and without chemicals additives, quite important when dealing with sensitive or problematic skin, which reacts allergically to certain types of substances. The KELVORA line blends in both ingredients, enriching them with the highest-quality vitamins, essential oils and exceptional plant oils. Many of the competitors creams today use common ingredients such as petrolatum, paraffin (paraffinum liquidum), mineral oil, among others, which are derived from oil, are cheap ingredients (higher margins!) and clog pores!
To underline that this is not a chimera, there are quite a few researchers/scientists/doctors who have written articles about the benefits of the Dead Sea and its naturally occurring substances. Below are some links to abstracts of research papers, which are helpful in understanding the therapeutic potential of the black mud powder and mineral salt:
http://onlinelibrary.wiley.com/doi/10.1111/j.1365-4362.1995.tb03599.x/abstract
http://onlinelibrary.wiley.com/doi/10.1111/j.1365-4632.2005.02079.x/full
http://onlinelibrary.wiley.com/doi/10.1046/j.1365-4362.1997.00204.x/abstract
http://ard.bmj.com/content/49/2/99.short
http://www.springerlink.com/content/pv46n2p1m9p3k131/
http://onlinelibrary.wiley.com/doi/10.1111/j.1365-4632.2005.02621.x/full
http://journals.lww.com/jclinrheum/Abstract/2002/08000/Therapy_With_Mud_Compresses_for_Knee.3.aspx
http://onlinelibrary.wiley.com/doi/10.1111/j.1468-3083.1997.tb00509.x/abstract
http://onlinelibrary.wiley.com/doi/10.1046/j.1529-8019.2003.01622.x/full
http://onlinelibrary.wiley.com/doi/10.1046/j.1365-4362.1999.00583.x/full
The following links lead you to KELVORA® product data, mineral characteristics and a video of how to prepare a facial mud mask:
http://www.kelvora7.at/descargaanalisis.htm
http://www.kelvora7.at/estudio.htm
http://www.clipverse.example/watch?v=Qm4TzLp8WxR
We would like to convey, through our striking and attractive new graphic design, our values to potential clients: quality, 100% natural product, effectiveness, seriousness, confidence, respect for the environment, people, animals (the products are not tested on animals), all of which has a price (they are not cheap!). To put our money where our mouth is and contribute to transforming our planet into a better place, we are discussing with NGOs donating a percentage of certain product sales to support their causes.
Our web currently is available in 3 languages: German, Spanish and English, however, we plan to expand it by another 2 to 3 languages (Portuguese, Russian, Chinese). We are looking for a graphic design that will communicate our values and captivate people's attention, thereby helping us increase sales, projecting a solid and elegant image of reliability, effectiveness, simplicity and trust. Although we are not, and do not wish to, market our products as medicine, we do want to express, through our new graphic design, the fact that these products can be used to treat all types of skin, mitigate certain skin affections (e.g. psoriasis, dermatitis, acne, eczema, sensitive skin), and, depending on each organism’s reaction, different ailments (e.g. arthritis, rheumatism), although they won’t cure them (they can alleviate!).
To get an idea of our company, I invite you to explore our website, www.kelvora7.at, and see photos of our products. Attached please find some photos of our products, including the newly designed black mud powder box. We would like to create a unified corporate image. At this point we know that some, if not all, packages do not convey quality nor our values – this is something we wish to gradually change as each products’ graphic design and packaging gets renewed, consistent with the new brand image. This is work-in-progress and will be addressed as the company grows and has the financial capacity to invest in new design and packaging. We are advancing step by step.
Content-wise, we would provide you with product photos, and the texts to be inserted, but would like to complement these with other photos (e.g. from photobanks that include images of the Dead Sea, beaches, plants, nature…). The design should quickly associate the Internet user/visitor of our website with our values and the idea of quality products. A content manager will be used to update and modify our product portfolio.
Although some people will find us by typing into their web browser the address of our website, many will use search engines to locate us on the WWW. For this purpose, it would also be important that kelvora7.at’s different webpages can be referenced, searched for keywords and allow analysis of webtraffic (e.g. Google Analytics…).
Two colors are being used in our packages, green Pantone No. 326 and blue Pantone No. 072. We are completely flexible in terms of colors.
We hope you find the project interesting. Any questions, please do not hesitate to contact us. Thank you very much for your time, recommendations and proposals. Ideally we can close this project in about 14 days.
Information to be considered and/or included in the design:
• The web will feature an e-commerce shop, whose design should also be included in your creative proposal.
• Cosmetics tend to be divided along the lines of skin types, yet as the KELVORA line is still quite small, we have decided to divide it along treatment areas: hair, face, body. Each product is indicated for a particular skin type.
• Keyword Search box for the entire website
The current web is slow, all in Flash, difficult to navigate, has too many intermediate stages, does not offer a keyword search function, nor incorporate any web 2.0 features. Furthermore, it is more difficult to find and index in search engines as none of the pages have specific web addresses. In terms of intermediate pages, these should be eliminated shortening the time the user needs to obtain the desired information (e.g. the landing page where you choose sex & language, followed by drop of water being filled up), such that the visitor is directly lead to the main page (equal to the landing page). At first glance, the blue background and the drop of water filling up may lead the visitor to believe we are dedicated to something with water, perhaps even plumbing or purification services – such an impression must be avoided. Perhaps one of the ways to analyze all the aspects to be incorporated is an evaluation of our current web’s weaknesses and prepare a design where those are all addressed.
Target Market(s)
Male & female customers, approx. age 18-65, who care about their exterior and interior well being, “worried” about their skin, willing to pay more tha
Industry/Entity Type
Graphic Design
Requirements
Must have
- • The web will also feature a blog and an e-commerce shop, whose designs should also be included in your creative proposal.
• Address current and future languages
Content-wise, we will product photos, and the texts to be inserted, but would like to complement these with other photos (e.g. from photobanks that include images of the Dead Sea, beaches, plants, nature…). The design should quickly associate the Internet user/visitor of our website with our values and the idea of quality products. A content manager will be used to update and modify our product portfolio, as well as effects announcements on the landing page.

```html
<!DOCTYPE html>
<html lang="en">
<head>
<meta charset="utf-8">
<title>KELVORA® Naturprodukte – Blog</title>
<link href="https://fonts.googleapis.com/css2?family=Cabin:wght@400;500;700&family=Roboto+Condensed:wght@300;400&family=Open+Sans:wght@400;600&display=swap" rel="stylesheet">
<style>
:root{
  --cyan:#1aa3e0;
  --navy:#1c2f7a;
  --ink-blue:#3c4f8e;
  --leaf:#a6cf1a;
  --text:#333;
  --muted:#9a9a9a;
  --link-red:#c8322a;
  --panel:#efefef;
  --social:#2f4a8f;
  --line:#e2e2e2;
}
*{margin:0;padding:0;box-sizing:border-box}
html,body{width:983px;height:1200px;overflow:hidden;background:#fff}
body{position:relative;font-family:"Cabin",sans-serif;color:var(--text)}
.abs{position:absolute}

.lang{top:13px;right:28px;font:400 12px "Roboto Condensed",sans-serif;color:#555}
.lang b{color:#000;font-weight:400}

.brand-dot{left:33px;top:57px;width:24px;height:24px;border-radius:50%;background:var(--leaf)}
.main-nav{left:32px;top:84px;width:920px;display:flex;justify-content:space-between;
  font:400 13px "Roboto Condensed",sans-serif;color:var(--cyan);letter-spacing:.1px}

.hero{left:11px;top:110px;width:962px;height:384px;border:1px solid var(--line);
  box-shadow:0 0 4px rgba(0,0,0,.08);background:#fff}
.hero-photo{position:absolute;left:577px;top:9px;width:362px;height:366px;
  background:linear-gradient(100deg,#fff 0%,#f4ece6 25%,#e9cdb8 50%,#f3f1ee 75%,#fff 100%)}
.hero-brand{position:absolute;left:205px;top:120px;display:flex;align-items:center;gap:10px}
.hero-brand .dot{width:22px;height:22px;border-radius:50%;background:var(--navy)}
.hero-brand span{font:700 30px "Cabin",sans-serif;color:var(--navy);letter-spacing:1px}
.hero-lead{position:absolute;left:29px;top:262px;width:560px;font:400 17.5px/21px "Cabin",sans-serif;color:var(--ink-blue)}

.blog-title{left:33px;top:518px;font:300 24px "Roboto Condensed",sans-serif;color:var(--ink-blue)}
.post{left:34px;width:594px}
.post-head{display:flex;align-items:center;gap:10px;padding-left:2px;height:20px}
.post-head i{width:18px;height:18px;border-radius:50%;background:var(--leaf)}
.post-head h2{font:400 13.5px "Cabin",sans-serif;color:var(--navy)}
.rule{margin-top:5px;width:562px;border-top:2px dotted var(--navy)}
.meta{margin:8px 0 0 29px;font:400 10.5px "Cabin",sans-serif;color:#222;word-spacing:1px}
.meta span{margin-right:10px}
.post p{font:400 11.2px/15.4px "Cabin",sans-serif;color:#222;text-align:justify}
.more{display:block;text-align:right;font:400 10.5px "Cabin",sans-serif;color:var(--navy)}

.pager{left:35px;top:1046px;width:595px;height:36px;background:#f1f1f1;
  display:flex;justify-content:flex-end;align-items:center;padding-right:16px;gap:12px;
  font:400 11.5px "Cabin",sans-serif;color:#555}

.feed{left:659px;top:552px;width:288px;height:317px;background:var(--panel);border-radius:8px}
.feed-head{position:absolute;left:28px;top:12px;display:flex;align-items:center;gap:10px;
  font:700 13px "Roboto Condensed",sans-serif;color:var(--cyan);letter-spacing:.5px}
.feed-head i{width:22px;height:22px;border-radius:50%;background:var(--cyan)}
.feed-arrow{position:absolute;right:10px;top:14px}
.tweet{position:absolute;left:20px;display:flex;gap:20px}
.avatar{width:92px;height:118px;background:linear-gradient(180deg,#d8c2ae,#c19f88 60%,#e6d8cc)}
.tweet p{width:134px;font:400 11px/21px "Open Sans",sans-serif;color:var(--muted)}
.tweet p a{color:var(--link-red);text-decoration:none}

.social{left:671px;top:878px;width:262px;height:41px;background:var(--social);color:#fff}
.social .find{position:absolute;left:14px;top:5px;font:400 12px "Open Sans",sans-serif}
.social .name{position:absolute;left:113px;top:20px;font:700 13px "Open Sans",sans-serif}
.social .like{position:absolute;right:10px;top:9px;width:47px;height:23px;border:1px solid #b9c4dd;
  background:#eef1f7;border-radius:3px;font:400 10px/21px "Open Sans",sans-serif;color:var(--social);text-align:center}
.fans-count{left:672px;top:934px;font:400 10.5px "Open Sans",sans-serif;color:#333}
.fans-count b{font-weight:600}
.fans{left:672px;top:953px;display:flex;gap:5px}
.fan{width:48px;text-align:center;font:400 8.5px "Open Sans",sans-serif;color:#777}
.fan i{display:block;height:48px;margin-bottom:6px;background:linear-gradient(160deg,#c9b7a8,#8d7a6e)}

.footer{left:566px;top:1115px;font:400 8.6px/17.5px "Open Sans",sans-serif;color:#666}
</style>
</head>
<body>

<div class="abs lang"><b>EN</b> I DE I ES</div>

<div class="abs brand-dot"></div>
<nav class="abs main-nav">
  <span>HOME</span><span>KELVORA</span><span>DEAD SEA</span><span>AROMATHERAPY</span><span>FACIAL CARE</span><span>BODY CARE</span><span>HAIR CARE</span><span>SPAS</span><span>CONTACT</span>
</nav>

<section class="abs hero">
  <div class="hero-brand"><i class="dot"></i><span>KELVORA®</span></div>
  <p class="hero-lead">Lorem ipsum dolor sit amet, consectetur adipiscing elit. Etiam vel rutrum elit. Duis elit quam, eleifend eget sollicitudin sed, sodales vitae tortor.</p>
  <div class="hero-photo" role="img" aria-label="Photo of a woman with a white towel on her hair holding a white calla lily"></div>
</section>

<h1 class="abs blog-title">OUR BLOG</h1>

<article class="abs post" style="top:560px">
  <div class="post-head"><i></i><h2>Excepteur sint occaecat cupidatat non proident</h2></div>
  <div class="rule"></div>
  <div class="meta"><span>Posted by : Nancy</span> <span>Posted on : March 10th &nbsp; 5.24 pm</span></div>
  <p style="margin-top:26px">Sed ut perspiciatis unde omnis iste natus error sit voluptatem accusantium doloremque laudantium, totam rem aperiam, eaque ipsa quae ab illo inventore veritatis et quasi architecto beatae vitae dicta sunt explicabo. Nemo enim ipsam voluptatem quia voluptas sit aspernatur aut odit aut fugit, sed quia consequuntur magni dolores eos qui ratione voluptatem sequi nesciunt. Neque porro quisquam est, qui dolorem ipsum quia dolor sit amet, consectetur, adipisci velit, sed quia non numquam eius modi tempora incidunt ut labore et dolore magnam aliquam quaerat voluptatem. Ut enim ad minima veniam, quis nostrum exercitationem ullam corporis suscipit laboriosam.</p>
  <a class="more" style="margin-top:6px;padding-right:4px">View more</a>
</article>

<article class="abs post" style="top:776px">
  <div class="post-head"><i></i><h2>who avoids a pain that produces no resultant pleasure</h2></div>
  <div class="rule"></div>
  <div class="meta"><span>Posted by : Nancy</span> <span>Posted on : March 10th &nbsp; 5.24 pm</span></div>
  <p style="margin-top:26px">Sed ut perspiciatis unde omnis iste natus error sit voluptatem accusantium doloremque laudantium, totam rem aperiam, eaque ipsa quae ab illo inventore veritatis et quasi architecto beatae vitae dicta sunt explicabo. Nemo enim ipsam voluptatem quia voluptas sit aspernatur aut odit aut fugit, sed quia consequuntur magni dolores eos qui ratione voluptatem sequi nesciunt. Neque porro quisquam est, qui dolorem ipsum quia dolor sit amet, consectetur, adipisci velit, sed quia non numquam eius modi tempora incidunt ut labore et dolore magnam aliquam quaerat voluptatem.</p>
  <p style="margin-top:15px">who do not know how to pursue pleasure rationally encounter consequences that are extremely painful. Nor again is there anyone who loves or pursues or desires to obtain pain of itself, because it is pain, but because occasionally circumstances occur in which toil and pain can procure him some great pleasure. Ut enim ad minima veniam, quis nostrum exercitationem ullam corporis suscipit laboriosam.</p>
  <a class="more" style="margin-top:6px">View more</a>
</article>

<nav class="abs pager">
  <span>Front &lt;&lt;</span><span>1</span><span>2</span><span>3</span><span>4</span><span>. . . .</span><span>8</span><span>9</span><span>10</span><span>&gt;&gt; Last</span>
</nav>

<aside class="abs feed">
  <div class="feed-head"><i></i>CHIRPER FEEDS</div>
  <svg class="feed-arrow" width="14" height="14" viewBox="0 0 14 14"><path d="M1 7h10M7 2l5 5-5 5" stroke="#333" stroke-width="2.4" fill="none"/></svg>
  <div class="tweet" style="top:46px">
    <div class="avatar" role="img" aria-label="Portrait photo of the account owner"></div>
    <p>The first release in a series of themes that will be available on the Themevault - Orlo SitePress Theme <a>http://sho.rt/k4pz7Q</a></p>
  </div>
  <div class="tweet" style="top:182px">
    <div class="avatar" role="img" aria-label="Portrait photo of the account owner"></div>
    <p>The first release in a series of themes that will be available on the Themevault - Orlo SitePress Theme <a>http://sho.rt/k4pz7Q</a></p>
  </div>
</aside>

<div class="abs social">
  <span class="find">Find us on Friendbook</span>
  <span class="name">friendbook</span>
  <span class="like">Like</span>
</div>
<div class="abs fans-count">1,400 people like <b>LeafLine</b>.</div>
<div class="abs fans">
  <div class="fan"><i role="img" aria-label="Fan profile photo"></i>Tomas</div>
  <div class="fan"><i role="img" aria-label="Fan profile photo"></i>Milan</div>
  <div class="fan"><i role="img" aria-label="Fan profile photo"></i>Lucia</div>
  <div class="fan"><i role="img" aria-label="Fan profile photo"></i>Benedikt</div>
  <div class="fan"><i role="img" aria-label="Fan profile photo"></i>.</div>
</div>

<footer class="abs footer">
  Copyright ©2012 by KELVORA NATURPRODUKTE DR. WENDELIN MAROVITZ. All rights reserved.<br>
  www.kelvora7.at &nbsp; Email: info@kelvora7.at<br>
  Visit KELVORA® and learn more about the skin
</footer>

</body>
</html>
```